Logo and Card design for KRV Home Solutions LLC

I need an edgier logo and business card designs. Current logo attached. I like the colors below. I would like the logo to incorporate a home in the design.
Title = Principal-Acquisitions
Email:KRVHOMESOLUTIONS@fernmail.example
555-214-0937
facebook
IG
2 sided business card with the front being contact info a slogan about selling a home fast. The back incorporating What we do. Buy houses, land, or commercial property as is. We find solutions to make the process of selling simple and fair.

Target Market(s)

Motivated house sellers.

Industry/Entity Type

Business

Contact Information for Business Card

Who we are: We are a Faith based Real Estate Investment Company. We pay cash for homes in any condition and can close quick. Whatever the reason you need to sell fast, we can help. We believe in creating win-win solutions to help you in your time of need. We care! We can help!

Logo Text

KRV Home Solutions LLC

Font styles to use
Sans Serif

Colors
33a6d7
0355a3
85abd2
cee9f5
9d9d9d
b2b2b2
ffffff

Requirements
Must have
• Old logo attached. I want something edgier.
• Company name, phone number, description on the back of what we can do. Pay all cash. Buy in as is condition. No fees,Commisions or closing costs.Close quick. No hassles with solutions to meet your unique situation.
• Call today for an offer within 24 hours.

```html
<!DOCTYPE html>
<html lang="en">
<head>
<meta charset="utf-8">
<title>KRV Home Solutions – Business Card</title>
<link rel="stylesheet" href="https://fonts.googleapis.com/css2?family=Roboto+Condensed:wght@400;700&family=Roboto:wght@400;700&display=swap">
<style>
  :root {
    --navy: #1e3566;
    --navy-deep: #1a2f5c;
    --ink: #3f4246;
    --ink-soft: #5a5d62;
    --rule: #9d9d9d;
    --white: #ffffff;
    --stage: #2a2a2a;
    --photo-sky: #dfe2ec;
    --photo-house: #c9c4bd;
  }
  * { box-sizing: border-box; margin: 0; padding: 0; }
  html, body { width: 1200px; height: 960px; overflow: hidden; }
  body { background: var(--stage); position: relative; font-family: "Roboto Condensed", Arial, sans-serif; }

  .card { position: absolute; width: 600px; height: 343px; overflow: hidden; box-shadow: 0 4px 10px rgba(0,0,0,.45); }

  /* Front */
  .card-front { left: 314px; top: 113px; background: var(--white); }
  .front-photo {
    position: absolute; left: 0; top: 0; width: 600px; height: 307px;
    background: linear-gradient(180deg, var(--photo-sky) 0%, #e4e3e6 40%, var(--photo-house) 75%, #d3d0cb 100%);
  }
  .front-rule { position: absolute; left: 0; top: 307px; width: 600px; height: 2px; background: var(--rule); }
  .front-band {
    position: absolute; left: 0; top: 309px; width: 600px; height: 34px; background: var(--navy);
    color: var(--white); font-family: "Roboto", Arial, sans-serif; font-size: 14px; letter-spacing: 2.4px;
    display: flex; align-items: center; justify-content: center;
  }
  .front-brand {
    position: absolute; left: 62px; top: 118px; width: 180px; text-align: center;
    color: var(--navy); font-weight: 700; font-size: 30px; line-height: 32px; text-transform: uppercase;
  }
  .front-divider { position: absolute; left: 268px; top: 57px; width: 1px; height: 195px; background: var(--ink-soft); }
  .contact { position: absolute; left: 297px; top: 58px; width: 290px; color: var(--ink); }
  .contact-name { color: var(--navy); font-size: 23px; font-weight: 700; line-height: 28px; }
  .contact-title { color: var(--ink-soft); font-size: 16px; line-height: 20px; }
  .contact-line { display: flex; align-items: center; gap: 7px; font-size: 15px; line-height: 19px; }
  .contact-line svg { width: 12px; height: 12px; fill: var(--navy); flex: none; }
  .contact-phone { margin-top: 8px; }
  .offer-list { list-style: none; margin-top: 8px; font-size: 14px; line-height: 18px; }
  .offer-list li { position: relative; padding-left: 13px; }
  .offer-list li::before { content: ""; position: absolute; left: 1px; top: 7px; width: 4px; height: 4px; border-radius: 50%; background: var(--navy); }

  /* Back */
  .card-back { left: 311px; top: 472px; background: var(--navy-deep); color: var(--white); text-align: center; font-family: "Roboto", Arial, sans-serif; }
  .back-brand { position: absolute; left: 0; top: 62px; width: 600px; font-family: "Roboto Condensed", Arial, sans-serif; font-weight: 700; font-size: 32px; line-height: 34px; text-transform: uppercase; }
  .back-heading { font-size: 15px; font-weight: 700; line-height: 20px; }
  .back-copy { font-size: 14.5px; line-height: 18px; }
  .who { position: absolute; left: 0; top: 168px; width: 600px; }
  .what { position: absolute; left: 0; top: 254px; width: 600px; }
</style>
</head>
<body>

<section class="card card-front" aria-label="Business card front">
  <div class="front-photo" role="img" aria-label="Soft faded photograph of a two-storey suburban house"></div>
  <div class="front-brand">KRV Home<br>Solutions</div>
  <div class="front-divider"></div>
  <div class="contact">
    <p class="contact-name">EVAN MARLOW</p>
    <p class="contact-title">Principal-Acquisitions</p>
    <p class="contact-line contact-phone">
      <svg viewBox="0 0 24 24" aria-hidden="true"><path d="M6.6 10.8a15.1 15.1 0 0 0 6.6 6.6l2.2-2.2a1 1 0 0 1 1-.25 11.4 11.4 0 0 0 3.6.57 1 1 0 0 1 1 1V20a1 1 0 0 1-1 1A17 17 0 0 1 3 4a1 1 0 0 1 1-1h3.5a1 1 0 0 1 1 1c0 1.25.2 2.45.57 3.57a1 1 0 0 1-.25 1z"/></svg>
      555-214-0937
    </p>
    <p class="contact-line">
      <svg viewBox="0 0 24 24" aria-hidden="true"><path d="M2 5h20v14H2zM3.5 6.5 12 12.5l8.5-6z" fill-rule="evenodd"/></svg>
      KRVHOMESOLUTIONS@fernmail.example
    </p>
    <ul class="offer-list">
      <li>Pay all cash. Buy in as is condition</li>
      <li>No fees,Commisions or closing costs</li>
      <li>Close quick. No hassles with<br>solutions to meet your unique situation</li>
      <li>Call today for an offer within 24 hours</li>
    </ul>
  </div>
  <div class="front-rule"></div>
  <div class="front-band">www.KRVHOMESOLUTIONS.example</div>
</section>

<section class="card card-back" aria-label="Business card back">
  <div class="back-brand">KRV Home<br>Solutions</div>
  <div class="who">
    <h2 class="back-heading">WHO WE ARE</h2>
    <p class="back-copy">We are a Faith based Real Estate Investment Company. We pay cash for<br>homes in any condition and can close quick. Whatever the reason you need<br>to sell fast, we can help. We believe in creating win-win solutions to help</p>
  </div>
  <div class="what">
    <h2 class="back-heading">WHAT WE DO</h2>
    <p class="back-copy">Buy houses, land, or commercial property as is.<br>We find solutions to make the process of selling simple and fair.</p>
  </div>
</section>

</body>
</html>
```